A new presentation to our clients

we are a Real Estate agency, our website is www.lumibrasa.com and it’s time to have a new, fashion and remarcable Business Card. we want to differentiate ourselves from other companies so we want a business card that differentiates us. we want the business card to impact our customers. in the competitive market that we have today, we have to be different and it is this difference that we seek

Target Market(s)

Real Estate Clients

Contact Information for Business Card

We search a totaly diferent card from the usual

Font styles to use
Sans Serif

Colors
e34197

Requirements
Must have
• Logo, adress, phone contact, e-mail, photo, and our website
Nice to have
• We would like to see a modern business card
Should not have
• Houses or building draws

```html
<!DOCTYPE html>
<html lang="en">
<head>
<meta charset="utf-8">
<title>Lumibrasa Business Card</title>
<link rel="stylesheet" href="https://fonts.googleapis.com/css2?family=Open+Sans:wght@400&family=Roboto:wght@500&display=swap">
<style>
  :root {
    --brand-pink: #e5226c;
    --backdrop: #6e6e6e;
    --card-white: #ffffff;
    --text-dark: #3d3d3d;
    --divider: #e4e4e4;
  }
  html, body {
    margin: 0;
    padding: 0;
    width: 1200px;
    height: 802px;
    overflow: hidden;
    background: var(--backdrop);
  }
  .canvas {
    position: relative;
    width: 1200px;
    height: 802px;
  }
  .card {
    position: absolute;
    top: 274px;
    width: 442px;
    height: 264px;
    box-shadow: 2px 3px 6px rgba(0, 0, 0, 0.45);
  }
  .card-front { left: 136px; background: var(--card-white); }
  .card-back { left: 624px; background: var(--brand-pink); }

  .wordmark {
    position: absolute;
    font-family: "Roboto", sans-serif;
    font-weight: 500;
    white-space: nowrap;
    line-height: 1;
  }
  .card-front .wordmark {
    left: 31px;
    top: 116px;
    font-size: 33px;
    color: var(--brand-pink);
  }
  .divider {
    position: absolute;
    left: 219px;
    top: 65px;
    width: 1px;
    height: 140px;
    background: var(--divider);
  }
  .contact {
    position: absolute;
    left: 238px;
    top: 67px;
    font-family: "Open Sans", sans-serif;
    font-size: 13px;
    line-height: 15.6px;
    color: var(--text-dark);
  }
  .contact-name {
    font-family: "Roboto", sans-serif;
    font-weight: 500;
    font-size: 16px;
    line-height: 18px;
    color: var(--brand-pink);
  }
  .contact-role { margin-bottom: 4px; }
  .contact-line { display: flex; align-items: center; gap: 4px; }
  .contact-line svg { width: 10px; height: 10px; flex: none; }
  .contact-address { margin-top: 4px; }

  .card-back .wordmark {
    left: 0;
    right: 0;
    top: 110px;
    text-align: center;
    font-size: 45px;
    color: var(--card-white);
  }
  .tagline {
    position: absolute;
    left: 0;
    right: 0;
    top: 172px;
    text-align: center;
    font-family: "Roboto", sans-serif;
    font-weight: 500;
    font-size: 12.5px;
    letter-spacing: 0.9px;
    color: rgba(255, 255, 255, 0.85);
  }
</style>
</head>
<body>
<div class="canvas">
  <section class="card card-front">
    <div class="wordmark">Lumibrasa</div>
    <div class="divider"></div>
    <div class="contact">
      <div class="contact-name">MARTA RIBEIRO</div>
      <div class="contact-role">Managing Director</div>
      <div class="contact-line">
        <svg viewBox="0 0 10 10" aria-hidden="true"><path fill="var(--brand-pink)" d="M1 3.5 Q5 0.5 9 3.5 L8 5 L6.5 4 L6.5 3.2 Q5 2.7 3.5 3.2 L3.5 4 L2 5 Z M2.5 6 H7.5 V9 H2.5 Z"/></svg>
        <span>(+351) 220 000 481</span>
      </div>
      <div class="contact-line">
        <svg viewBox="0 0 10 10" aria-hidden="true"><path fill="var(--brand-pink)" d="M3 1 H7 V3 H3 Z M1 3.5 H9 V7.5 H7.5 V6 H2.5 V7.5 H1 Z M3 6.5 H7 V9 H3 Z"/></svg>
        <span>(+351) 220 000 482</span>
      </div>
      <div class="contact-line">
        <svg viewBox="0 0 10 10" aria-hidden="true"><rect x="1" y="2.5" width="8" height="5.5" fill="var(--brand-pink)"/><path d="M1.3 2.8 L5 5.8 L8.7 2.8" stroke="#fff" stroke-width="0.8" fill="none"/></svg>
        <span>geral@lumibrasa.com</span>
      </div>
      <div class="contact-line">
        <svg viewBox="0 0 10 10" aria-hidden="true"><circle cx="5" cy="5" r="4.3" fill="var(--brand-pink)"/><path d="M3 3.5 Q4.5 3 5 4.5 Q4 6 5.5 7.5 M6 2 Q7 3.5 8 4" stroke="#fff" stroke-width="0.8" fill="none"/></svg>
        <span>www.lumibrasa.com</span>
      </div>
      <div class="contact-address">Rua do Sol Poente, 57<br>4410-082, Vila Nova de Gaia</div>
    </div>
  </section>

  <section class="card card-back">
    <div class="wordmark">Lumibrasa</div>
    <div class="tagline">THE HOUSE OF YOUR DREAMS!</div>
  </section>
</div>
</body>
</html>
```